New and upgraded www.valdmorefunds.com content & design financial markets

We need an upgrade of our site. The current site is www.valdmorefunds.com
Navigation with full site map i.e. the user can select any page from any menu item.

The “Insights” (Insikter) page will remain as is except new design AND with far more possibilities to add thumbnails, picts, videos etc. The user will have to logon to be able to read the full story.

The “Produkter & Tjänster” (“How to invest” in current web) will contain about the same info as the current “How to invest” pages.

Some pages will contain one or more videos and or speaker supported “live” graphics which we will supply. The media content shall be easy to change.

The site will have two languages from start, English and Swedish. There will be more languages added within 1 year or slightly more.

All texts will be provided by us.

I’m attaching a PDF with suggested content for some of the new pages. However this is just content and absolutely no design. We need new design for the total of the site as well as for the graphics.

Expectation info:
These sites (Both major players in our business) can be used as inspiration:
https://www.tarvenholm.com/eu/en/
https://www.brightwellpartners.com/index.html

Below some opt-OUT and opt-IN graphic rules in connection with the Web supporting our business acumen and brand:

Opt-OUT:
- images similar to educational comic books - it signals an authoritarian approach where the customer is small (insubstantial).
- images that signal trading, cyber, mystery and fast-paced business. We are extremely long-term and invest in real companies
- avoid images containing coins, calculators and banknotes. We're not a savings bank company. or payment service-branch
- avoid images of large data flows, because we should not make facts complex, but simple and comprehensible
- avoid sensing pictures of photo models. We are real people who stand for our efforts. We're not going to hide.
- avoid pictures of suits and tie. They signal rigid-banking. We're smart-investment, flexible, adaptable. Rather curl up your sleeves and show that we’re building something valuable.
- avoid pictures of skyscrapers and cool bank pictures - because they signal the more old valuations of big capital and giant banks - that we are not at all. I know we've had clean facades before. As long as we're not talking about bank skyscrapers, I'm in.

Opt-IN
- pictures of Lukas in moderate amount - he is our symbol person
- films with Lukas and explaining graphical films - explaining and clarifying
- images of pedagogy that give the customer a sense of overview and insights that we give to the customers in our service
- illustrations that explain and deepen our work
- pictures and bars that in 3d illustrate our consistent results and stable delivery
- images that signal that we have a full grasp of data, flows and analyses - without the image becoming a space adventure
- use the logo as a grid, shape and colour.
- no genre portraits, rather pictures of real customers - which gives a sense of why they are customers here
- images that support our core i.e. is science, innovation, unrestricted thinking (“out of the box” – (don’t like that sentence)), smart-solutions, data-driven, client-cantered, flexible and adaptable to client needs and expectation.
- Solid - to be trustworthy in any economic climate
- Long term - consistent work and choices. No trading. Numbers talk
- Data-driven - real tech - combining years of work in finance with straight on tech

Presenting on the webpage:
The story in text and illustration
Show the truth - we have a great history to show and give space
Only numbers and graphs that has a meaning - no artificial numbers etc.
Updates

Target Market(s)

Europe

Coding

Coded - Design and coding required

Number of Pages Required

5+ page

Colors

Designer to choose colors to be used in the design.

Requirements
Must have
• Colours in line with www.valdmorefunds.com

```html
<!DOCTYPE html>
<html lang="en">
<head>
<meta charset="utf-8">
<title>Valdmore Capital – Your Personal Investment Advisor</title>
<link rel="stylesheet" href="https://fonts.googleapis.com/css2?family=Poppins:wght@300;400;500;600;700&family=Open+Sans:wght@400;600&display=swap">
<style>
:root{
  --navy:#0c1657;
  --brand:#2443a3;
  --deep:#0f35a3;
  --ink:#2c2f3a;
  --muted:#6b7590;
  --pale:#e3e9f6;
  --numeral:#c7cfe2;
  --footer:#0a0e3b;
  --white:#ffffff;
}
*{box-sizing:border-box;margin:0;padding:0}
html,body{width:1200px;height:3072px;overflow:hidden}
body{position:relative;background:var(--white);font-family:"Open Sans",sans-serif;color:var(--ink)}
.abs{position:absolute}

/* header */
.site-header{position:absolute;left:0;top:0;width:1200px;height:63px;background:var(--white);z-index:3}
.brand{position:absolute;left:143px;top:20px;display:flex;align-items:center;gap:10px;font-family:"Poppins",sans-serif;font-size:25px;font-weight:400;color:var(--navy);line-height:1}
.brand-square{width:20px;height:20px;background:var(--navy)}
.main-nav a{position:absolute;top:28px;font-family:"Poppins",sans-serif;font-size:12.5px;color:var(--ink);text-decoration:none;letter-spacing:.2px;white-space:nowrap}
.main-nav a.is-active{color:var(--brand)}
.lang{position:absolute;top:29px}

/* hero */
.hero{position:absolute;left:0;top:63px;width:1200px;height:631px;overflow:hidden}
.hero-visual{position:absolute;inset:0;background:linear-gradient(100deg,#b9c7d8 0%,#dbe4ee 30%,#a9b6c6 55%,#cfd9e6 75%,#9fb0c4 100%)}
.hero-title{position:absolute;left:144px;top:160px;font-family:"Poppins",sans-serif;font-weight:700;font-size:42px;line-height:48px;color:var(--navy);letter-spacing:-.3px}
.btn{display:block;position:absolute;background:var(--brand);color:var(--white);font-family:"Poppins",sans-serif;font-weight:500;font-size:16px;text-align:center;text-decoration:none}
.hero .btn{left:144px;top:264px;width:176px;height:46px;line-height:46px}
.hero-arrow{position:absolute;top:258px}

/* intro */
.quote{position:absolute;left:0;top:765px;width:1200px;text-align:center;font-family:"Poppins",sans-serif;font-weight:400;font-size:33px;line-height:48px;color:var(--navy)}
.quote-by{position:absolute;left:0;top:876px;width:1200px;text-align:center;font-family:"Poppins",sans-serif;font-size:19.5px;color:var(--brand)}
.intro-text{position:absolute;left:146px;top:922px;width:908px;text-align:center;font-size:13px;line-height:24px;color:var(--ink)}
.intro .btn{left:540px;top:1038px;width:120px;height:38px;line-height:38px;font-size:15px}

/* approach */
.approach{position:absolute;left:0;top:1157px;width:1200px;height:662px;background:var(--pale)}
.section-title{position:absolute;left:0;width:1200px;text-align:center;font-family:"Poppins",sans-serif;font-weight:400;font-size:34px;color:var(--navy)}
.approach-sub{position:absolute;left:0;top:170px;width:1200px;text-align:center;font-family:"Poppins",sans-serif;font-size:19.5px;line-height:32px;color:var(--brand)}
.card{position:absolute;top:260px;width:280px;height:281px;background:var(--white);box-shadow:0 2px 8px rgba(20,40,100,.12);padding:14px 20px 0}
.card-num{font-family:"Poppins",sans-serif;font-weight:300;font-size:92px;line-height:92px;color:var(--numeral);letter-spacing:-2px}
.card-rule{width:80px;height:4px;background:var(--brand);margin-top:2px}
.card-title{margin-top:19px;font-family:"Poppins",sans-serif;font-weight:400;font-size:16.5px;line-height:22px;color:var(--brand)}
.card-text{margin-top:12px;font-size:10.5px;line-height:19px;color:var(--ink)}

/* philosophy */
.tabs{position:absolute;left:144px;top:1905px;width:488px}
.tab{height:64px;border-bottom:1px solid #c9d0e2;display:flex;align-items:center;gap:13px;font-family:"Poppins",sans-serif;font-size:21.5px;letter-spacing:-.2px;white-space:nowrap;color:#7d879f}
.tab.is-open{color:var(--navy)}
.tab .dot{width:8px;height:8px;border-radius:50%;background:#7d879f;margin-left:1px;flex:none}
.tab svg{flex:none}
.tabs-line{position:absolute;left:632px;top:1902px;width:1px;height:460px;background:#c9d0e2}
.tab-marker{position:absolute;left:629px;top:1922px}
.video-thumb{position:absolute;left:143px;top:2168px;width:475px;height:195px;background:linear-gradient(90deg,#b7905a 0%,#e4c79a 30%,#6c5d52 50%,#8d7d6e 70%,#d7c6a4 100%)}
.play-btn{position:absolute;left:143px;top:2324px;width:136px;height:39px;background:var(--brand);color:var(--white);font-family:"Poppins",sans-serif;font-size:15.5px;display:flex;align-items:center;gap:8px;padding-left:12px}
.feature-photo{position:absolute;left:672px;top:1918px;width:383px;height:235px;background:linear-gradient(120deg,#c6ccd6 0%,#eef0f3 45%,#f4efe6 70%,#dbe0e7 100%)}
.feature-list{position:absolute;left:672px;top:2172px;width:390px;list-style:none}
.feature-list li{position:relative;padding-left:16px;font-size:11.5px;line-height:19px;color:var(--ink);margin-bottom:8px}
.feature-list li::before{content:"";position:absolute;left:2px;top:7px;width:4px;height:4px;border-radius:50%;background:var(--ink)}

/* contact */
.contact{position:absolute;left:0;top:2446px;width:1200px;height:500px;background:var(--pale)}
.field{position:absolute;background:var(--white);border:1px solid #c4cbdc;font-size:11.5px;color:#7b8296;padding:12px 15px}
.contact .btn{left:540px;top:378px;width:120px;height:38px;line-height:38px;font-size:15px}

/* footer */
.site-footer{position:absolute;left:0;top:2941px;width:1200px;height:131px;background:var(--footer)}
.footer-nav{position:absolute;left:144px;top:60px;font-size:12px;color:#8f9bd0}
.footer-nav span{margin:0 9px;color:#8f9bd0}
.copyright{position:absolute;left:144px;top:91px;font-size:12px;color:#8f9bd0}
.social{position:absolute;top:74px;width:18px;height:18px;border-radius:50%;background:#8f9bd0}
</style>
</head>
<body>

<header class="site-header">
  <div class="brand"><span class="brand-square"></span>Valdmore Capital</div>
  <nav class="main-nav">
    <a class="is-active" style="left:420px">RESULT</a>
    <a style="left:492px">METHOD</a>
    <a style="left:574px">INSIGHTS</a>
    <a style="left:658px">QUESTIONS &amp; ANSWERS</a>
    <a style="left:830px">CONTACT</a>
    <a style="left:914px">VALDMORE</a>
  </nav>
  <svg class="lang" style="left:1010px" width="20" height="13" viewBox="0 0 20 13" aria-label="English">
    <rect width="20" height="13" fill="#1f3a8a"/>
    <path d="M0 0L20 13M20 0L0 13" stroke="#fff" stroke-width="3"/>
    <path d="M0 0L20 13M20 0L0 13" stroke="#c8102e" stroke-width="1"/>
    <path d="M10 0V13M0 6.5H20" stroke="#fff" stroke-width="4"/>
    <path d="M10 0V13M0 6.5H20" stroke="#c8102e" stroke-width="2"/>
  </svg>
  <svg class="lang" style="left:1041px" width="20" height="13" viewBox="0 0 20 13" aria-label="Svenska">
    <rect width="20" height="13" fill="#1d5fa8"/>
    <path d="M7.5 0V13M0 6.5H20" stroke="#f5c400" stroke-width="2.6"/>
  </svg>
</header>

<section class="hero">
  <div class="hero-visual" role="img" aria-label="Photo of stacked investment tokens in front of rising market charts and a faint world map"></div>
  <h1 class="hero-title">YOUR PERSONAL<br>INVESTMENT ADVISOR</h1>
  <a class="btn">GET STARTED NOW</a>
  <svg class="hero-arrow" style="left:52px" width="32" height="36" viewBox="0 0 32 36"><path d="M24 3L8 18L24 33" fill="none" stroke="#fff" stroke-width="7"/><path d="M24 3L8 18L24 33" fill="none" stroke="var(--navy)" stroke-width="3.5"/></svg>
  <svg class="hero-arrow" style="left:1114px" width="32" height="36" viewBox="0 0 32 36"><path d="M8 3L24 18L8 33" fill="none" stroke="#fff" stroke-width="7"/><path d="M8 3L24 18L8 33" fill="none" stroke="var(--navy)" stroke-width="3.5"/></svg>
  <svg class="abs" style="left:0;top:551px" width="1200" height="80" viewBox="0 0 1200 80">
    <polygon points="0,0 597,40 0,80" fill="var(--deep)"/>
    <polygon points="0,80 597,40 1200,80" fill="var(--white)"/>
  </svg>
</section>

<section class="intro">
  <p class="quote">"Our portfolios are steadily<br>performing better than the stock exchange"</p>
  <p class="quote-by">- Lukas Brenmark, managing director of Valdmore.</p>
  <p class="intro-text">We are a privately held firm dedicated to clients who have entrusted us with their wealth. We act solely and transparently in the best interest of our clients. We pride ourselves on our discretion and confidentiality. You can be assured of a totally Client-centric service, high quality, totally unbiased, investment advice. We are fee only based, i.e. we have no affiliations with any financial institutions – we do not take any commission from any investment product provider – We Work Only for You!</p>
  <a class="btn">READ MORE</a>
</section>

<section class="approach">
  <svg class="abs" style="left:0;top:0" width="1200" height="40" viewBox="0 0 1200 40">
    <polygon points="0,0 799,26 1200,0" fill="var(--white)"/>
    <polygon points="799,26 1200,0 1200,38" fill="var(--deep)"/>
  </svg>
  <h2 class="section-title" style="top:110px">Our Approach</h2>
  <p class="approach-sub">Valdmore Capital is truly different –<br>We deliver Investment Services that sets us apart from our contemporaries.</p>

  <article class="card" style="left:144px">
    <div class="card-num">01</div><div class="card-rule"></div>
    <h3 class="card-title">Valdmore Investment<br>Management System VIMS®</h3>
    <p class="card-text">Built on a combination of macroeconomic and fundamental analysis.</p>
  </article>
  <article class="card" style="left:460px">
    <div class="card-num">02</div><div class="card-rule"></div>
    <h3 class="card-title">VIQS ®<br>Investment Generator</h3>
    <p class="card-text">Valdmore iQ Software VIQS® is designed to analyse, forcast, generate and monitor an infinite number of personalized investment portfolios in a fully automated process &amp; digital system</p>
  </article>
  <article class="card" style="left:775px">
    <div class="card-num">03</div><div class="card-rule"></div>
    <h3 class="card-title">Services</h3>
    <p class="card-text" style="margin-top:34px">VIMS® &amp; VIQS® enable Valdmore Capital to deliver customized services &amp; solutions to low cost &amp; risks with predictable returns.</p>
  </article>

  <svg class="abs" style="left:0;top:623px" width="1200" height="40" viewBox="0 0 1200 40">
    <polygon points="0,39 394,13 1200,39" fill="var(--white)"/>
    <polygon points="0,0 394,13 0,39" fill="var(--deep)"/>
  </svg>
</section>

<section class="philosophy">
  <div class="tabs">
    <div class="tab is-open"><svg width="10" height="14" viewBox="0 0 10 14"><path d="M2 2L8 7L2 12" fill="none" stroke="var(--navy)" stroke-width="1.6"/></svg>Valdmore Investment Advisory Philosophy</div>
    <div class="tab"><span class="dot"></span>Valdmore Capital Investment Strategy</div>
    <div class="tab"><span class="dot"></span>Investment Intelligence</div>
    <div class="tab"><span class="dot"></span>Client Focus</div>
  </div>
  <div class="tabs-line"></div>
  <svg class="tab-marker" width="18" height="30" viewBox="0 0 18 30"><polygon points="0,0 8,0 17,15 8,30 0,30" fill="var(--deep)"/></svg>
  <div class="video-thumb" role="img" aria-label="Video still of the managing director speaking in a bright office corridor"></div>
  <div class="play-btn"><svg width="19" height="19" viewBox="0 0 19 19"><circle cx="9.5" cy="9.5" r="9.5" fill="#fff"/><polygon points="7,5 14,9.5 7,14" fill="var(--brand)"/></svg>PLAY VIDEO</div>
  <div class="feature-photo" role="img" aria-label="Photo of an advisor working through figures at a desk beside a laptop"></div>
  <ul class="feature-list">
    <li>Systematic Adaption to Market Climate</li>
    <li>Attractive Risk Returns with Low Portfolio Turnover</li>
    <li>Europe and U.S. Investment Area</li>
    <li>Built to Follow or Outperform the Market During Upturns and Avoid Large Declines During Long – Term Market Turndowns</li>
    <li>Continuously Monitoring, Identifying and Implementing to Maintain Optimal Portfolio</li>
    <li>Long – Term Investment Strategy</li>
  </ul>
</section>

<section class="contact">
  <svg class="abs" style="left:0;top:0" width="1200" height="40" viewBox="0 0 1200 40">
    <polygon points="0,0 811,26 1200,0" fill="var(--white)"/>
    <polygon points="811,26 1200,0 1200,38" fill="var(--deep)"/>
  </svg>
  <h2 class="section-title" style="top:103px">Contact Us</h2>
  <div class="field" style="left:259px;top:165px;width:218px;height:40px">Name</div>
  <div class="field" style="left:491px;top:165px;width:218px;height:40px">Email</div>
  <div class="field" style="left:723px;top:165px;width:218px;height:40px">Phone</div>
  <div class="field" style="left:259px;top:220px;width:682px;height:128px">Message</div>
  <a class="btn">SUBMIT</a>
</section>

<footer class="site-footer">
  <svg class="abs" style="left:0;top:0" width="1200" height="40" viewBox="0 0 1200 40">
    <polygon points="0,0 1200,0 1200,38 560,20" fill="var(--pale)"/>
    <polygon points="0,0 560,20 0,26" fill="var(--deep)"/>
  </svg>
  <nav class="footer-nav">Result<span>|</span>Method<span>|</span>Insights<span>|</span>Questions &amp; Answers<span>|</span>Contact<span>|</span>Valdmore</nav>
  <p class="copyright">Copyright &nbsp;©&nbsp; 2019 &nbsp; Valdmore Capital. &nbsp; All rights reserved.</p>
  <span class="social" style="left:992px" aria-label="Social profile"></span>
  <span class="social" style="left:1036px" aria-label="Social profile"></span>
</footer>

</body>
</html>
```